$5 Quest Website Required

I am looking for someone to develop a website akin to the simplicity of www.boxlantern.example with a video in the center or a tab that permits one to "Accept the Challenge."

Incorporates our logo and is used to promote our "$5 Quest Program."

Please see attachments, but we are igniting entrepreneurial spirit among our nation's youth through this interactive and intensive program!

There should be a way to navigate to other sections of the site including:

About
Why
Request $5 Quest Packet
Success Stories
Partners
Link to Norvik Holdings
Updates

Thanks to all in advance!

Looking forward to working with you!

Good feel of what we are looking for in terms of "feel"

http://www.thebrightripple.example/

Thank you,

RB

Please make note of this website, we are going for a feel that is akin to this and less modern and professional...more abstract and interactive...but of course include space for our video:

Colors, feel, imagery, is great. Keep your formats, but bring on the feel!

Thank you all for your hard work and patience.

Thank you all for your hard work thus far.

Meanwhile, please understand that the $5 Quest is young, youthful, full of challenge and vitality, it is a competition among students from high school and universities.  The websites you have delivered are too corporate, stale, and standard.  I'm looking for something that is fresh, different, like www.thebrightripple.example.

Symbols, cartoonish, but serious, down to business and save the world one $5 bill at a time.  The logo can be used as a theme...the colors, the feel.

Video space for explanation on the $5 Quest front and center.  With leaves, $ signs, colorful colors, etc.

Visual needs to be compelling to Join the Challenge! Although Norvik Holdings and the tree is a parent company; $5 Quest is separate and Norvik Holdings should only be mentioned as a link.

PixelHarbor.example in regard to simplicity; and www.thebrightripple.example in terms of style.

Thank you,

Raphael

Like the designs that have been submitted; we are almost there.

Target Market(s)

Professors, students, teachers, parents and NGO leaders who wish to use our program as a way to inspire leadership/entrepreneurship/fundraise for their causes.

Requirements
Must have
• Place for the video, front and center
Include logo
Forsight for blogging, message, etc.
Nice to have
• Plan "buckets" to include"
Explanation Video
Two pamphlets
Contract
FAQs
Website with Blog, voting, registration, video upload, etc.
Flyer perfected
Parable...symbol of our life
Photos
Stats included
Testimonials
Organizations that have used (TKWLM, North Brook Lodge, Marlowton High)
Sponsors (Open Lantern, Copperleaf Learningfield)
Photos from events

I understand this takes coding and such, but want you to be aware of the long term vision for it!

```html
<!DOCTYPE html>
<html lang="en">
<head>
<meta charset="utf-8">
<title>$5 Quest</title>
<link href="https://fonts.googleapis.com/css2?family=Exo+2:wght@500;600;700&family=Ubuntu:wght@400;500;700&family=Roboto:wght@400;500&display=swap" rel="stylesheet">
<style>
:root{
  --cream:#f5f1e1;
  --cream-dark:#ebe5cf;
  --green:#2f9a3c;
  --green-dark:#1f7d2c;
  --lime:#b8c51a;
  --olive:#6f9a2a;
  --brown:#4a4030;
  --brown-dark:#2e271c;
  --ink:#555;
  --ink-soft:#6b6b6b;
  --white:#fff;
  --line:#ddd6bd;
}
*{box-sizing:border-box;margin:0;padding:0}
html,body{width:948px;height:1200px;overflow:hidden}
body{position:relative;background:linear-gradient(180deg,#f7f4e7 0%,var(--cream) 60%,#f1ecd8 100%);font-family:"Roboto",Arial,sans-serif;color:var(--ink)}
.abs{position:absolute}

/* header */
.brand{left:66px;top:26px;font-family:"Ubuntu",sans-serif;font-weight:700;font-size:42px;line-height:1;color:var(--ink)}
.parent-link{left:700px;top:12px;font-family:"Ubuntu",sans-serif;font-weight:500;font-size:11.5px;color:#555;text-decoration:underline}
.corner-ornament{border-radius:50%;background:radial-gradient(circle,rgba(160,190,130,.35),rgba(160,190,130,0) 70%)}
.main-nav{left:459px;top:64px;display:flex;align-items:center;font-family:"Ubuntu",sans-serif;font-size:11px;color:#555}
.main-nav a{color:inherit;text-decoration:none;margin-right:33px}
.main-nav a.active{background:var(--olive);color:var(--white);padding:5px 13px;border:1px solid #5b8220;box-shadow:0 0 0 2px #e9efd3;margin-right:18px}

/* hero */
.hero{left:0;top:100px;width:948px;height:330px;background:radial-gradient(ellipse at 60% 45%,#6e6550 0%,#574d3b 45%,var(--brown-dark) 100%)}
.hero-photo{left:108px;top:125px;width:229px;height:287px;background:linear-gradient(160deg,#cfc8bf,#a8a39b 55%,#d6a8c0);border:6px solid #f2efe8}
.hero-title{left:407px;top:130px;font-family:"Exo 2",sans-serif;font-weight:700;font-size:29px;color:var(--white);text-shadow:0 2px 2px rgba(0,0,0,.5)}
.hero-title span{color:var(--lime)}
.hero-text{left:405px;top:198px;width:420px;font-family:"Ubuntu",sans-serif;font-size:10.6px;line-height:19.8px;color:#f1ede2;text-align:justify}
.cta{left:412px;top:356px;width:176px;height:38px;border-radius:8px;background:linear-gradient(#5f9a26,#3e7416);border:2px solid #d8e69a;color:var(--white);font-family:"Ubuntu",sans-serif;font-size:17px;letter-spacing:.5px;display:flex;align-items:center;justify-content:center}
.slide-arrow{top:243px;width:34px;height:74px;background:#eee9dc;border:1px solid #cfc7b4}
.slide-arrow.prev{left:0}
.slide-arrow.next{left:914px}

/* columns */
.col-title{font-family:"Exo 2",sans-serif;font-weight:600;font-size:19px;color:var(--green)}
.col-text{left:84px;top:482px;width:211px;font-size:10px;line-height:16.5px;letter-spacing:.3px;text-align:justify;color:var(--ink-soft)}
.read-more{left:85px;top:602px;font-size:10.5px;color:var(--green-dark);font-weight:500}
.v-rule{width:1px;background:linear-gradient(transparent,var(--line),transparent)}
.video{left:363px;top:482px;width:226px;height:129px;border:3px solid #e6e2d6;background:linear-gradient(180deg,#7c8c6c,#3a3a3a 60%,#222)}
.video-bar{left:366px;top:601px;width:220px;height:7px;background:#1c1c1c}
.pamphlets{left:660px;top:480px;width:195px;height:132px;background:linear-gradient(100deg,#6f8c4c 0%,#e9e2cc 35%,#f0d430 60%,#e05ab0 85%,#f1e9f1 100%);transform:rotate(-3deg)}

/* blog + queries panel */
.panel{left:80px;top:637px;width:788px;height:188px;background:rgba(250,247,235,.85);border:1px dashed var(--line);border-radius:6px}
.sec-title{font-family:"Exo 2",sans-serif;font-weight:600;font-size:21px;color:var(--green)}
.sec-title span{color:var(--lime)}
.blog-sub{left:104px;top:695px;font-size:12.5px;color:#555}
.blog-text{left:104px;top:721px;width:450px;font-size:10px;line-height:17.5px;letter-spacing:.3px;color:#666}
.blog-meta{left:106px;top:803px;font-size:10.5px;color:#555}
.tweet{left:468px;top:798px;display:flex;align-items:center;gap:6px;font-size:11px;color:#555}
.tweet .pill{background:#eef1f4;border:1px solid #d5dbe2;border-radius:4px;padding:2px 8px 2px 4px;display:flex;align-items:center;gap:5px}
.tweet .pill i{width:14px;height:14px;border-radius:50%;background:#3aa0e0;display:block}
.tweet .count{border:1px solid #c9d2da;border-radius:50%;width:18px;height:18px;font-size:9px;display:flex;align-items:center;justify-content:center;background:#fff}
.dash-rule{left:591px;top:648px;height:176px;border-left:2px dashed var(--line)}
.q-icon{left:630px;top:654px;width:26px;height:24px;border-radius:50%;background:var(--green);color:#fff;font:700 15px "Ubuntu",sans-serif;display:flex;align-items:center;justify-content:center}
.form-label{left:634px;font-size:10.5px;color:#555}
.field{left:678px;width:148px;height:18px;border:1px solid #dcd6c0;border-radius:5px;background:#fbf9f1;box-shadow:inset 0 1px 2px rgba(0,0,0,.06)}
.submit{left:758px;top:804px;width:63px;height:19px;border-radius:6px;background:linear-gradient(#2fa34a,#17803a);color:#fff;font:500 10.5px "Roboto",sans-serif;display:flex;align-items:center;justify-content:center}

/* events */
.event-photo{top:897px;width:101px;height:101px;border:3px solid #fff;box-shadow:0 0 0 1px #ddd}

/* footer */
.footer{left:0;top:1025px;width:948px;height:175px;background:linear-gradient(#ebe5d0,#f1ecda 20%,var(--cream))}
.footer-top{left:0;top:1022px;width:948px;height:6px;background:repeating-linear-gradient(90deg,#ddd5bc 0 6px,#e8e1cc 6px 12px)}
.f-title{top:1040px;font-family:"Exo 2",sans-serif;font-weight:600;font-size:17px;color:var(--green)}
.f-links{left:71px;top:1075px;list-style:none;font-size:10.5px;line-height:20px;color:#555;letter-spacing:.3px}
.f-links li::before{content:"";display:inline-block;border-left:4px solid var(--green);border-top:3px solid transparent;border-bottom:3px solid transparent;margin-right:10px}
.quote-open{left:258px;top:1066px;font:700 16px/1 Georgia,serif;color:#777}
.quote-close{left:452px;top:1106px;font:700 16px/1 Georgia,serif;color:#777}
.quote{left:272px;top:1075px;width:196px;font-size:10px;line-height:16.5px;color:#555;text-align:justify}
.quote b{font-weight:500}
.author{left:410px;top:1134px;font-size:10.5px;font-weight:500;color:#555}
.badge{border-radius:50%;background:#d9d4c3}
.contact{left:721px;top:1073px;font-size:10px;line-height:20px;letter-spacing:.4px;color:#555}
.follow{left:735px;top:1160px;font-family:"Exo 2",sans-serif;font-weight:600;font-size:15px;color:var(--green)}
.social{top:1158px;width:20px;height:20px;border-radius:2px}
.copyright{left:71px;top:1172px;font-size:10.5px;color:#555}
</style>
</head>
<body>

<!-- header -->
<div class="abs corner-ornament" role="img" aria-label="Faint green floral corner ornament" style="left:800px;top:-20px;width:170px;height:110px"></div>
<div class="abs brand">$5 Quest</div>
<a class="abs parent-link">Norvik Holdings</a>
<nav class="abs main-nav">
  <a class="active">About</a>
  <a>Why Request $5 Quest Packet</a>
  <a>Success Stories</a>
  <a>Partners</a>
</nav>

<!-- hero -->
<section class="abs hero"></section>
<svg class="abs" style="left:0;top:94px" width="948" height="12" viewBox="0 0 948 12" preserveAspectRatio="none">
  <polygon fill="#554a37" points="0,12 0,6 20,3 40,7 60,2 85,6 110,3 140,7 170,2 200,6 230,3 260,7 290,2 320,6 350,3 380,7 410,2 440,6 470,3 500,7 530,2 560,6 590,3 620,7 650,2 680,6 710,3 740,7 770,2 800,6 830,3 860,7 890,2 920,6 948,3 948,12"/>
</svg>
<svg class="abs" style="left:0;top:424px" width="948" height="14" viewBox="0 0 948 14" preserveAspectRatio="none">
  <polygon fill="#2e271c" points="0,0 948,0 948,7 930,12 905,6 880,11 855,5 830,12 805,6 780,11 755,5 730,12 705,6 680,11 655,5 630,12 605,6 580,11 555,5 530,12 505,6 480,11 455,5 430,12 405,6 380,11 355,5 330,12 305,6 280,11 255,5 230,12 205,6 180,11 155,5 130,12 105,6 80,11 55,5 30,12 0,6"/>
</svg>
<div class="abs hero-photo" role="img" aria-label="Photo of a young girl standing against a weathered wooden wall"></div>
<h1 class="abs hero-title"><span>A program</span> about people</h1>
<p class="abs hero-text">Lorem Ipsum is simply dummy text of the printing and typesetting industry. Lorem Ipsum has been the industry's standard dummy text ever since the 1500s, when an unknown printer took a galley of type and scrambled it to make a type specimen book. It has survived not only five centuries, but also the leap into electronic typesetting, remaining essentially unchanged. It was popularised in the 1960s with the release of Letraset sheets</p>
<a class="abs cta">Accept Challenge</a>
<div class="abs slide-arrow prev"><svg width="34" height="74"><polygon points="22,24 12,37 22,50" fill="#b5ad9a"/></svg></div>
<div class="abs slide-arrow next"><svg width="34" height="74"><polygon points="12,24 22,37 12,50" fill="#b5ad9a"/></svg></div>

<!-- three columns -->
<div class="abs corner-ornament" role="img" aria-label="Faint green leaf ornament" style="left:-20px;top:420px;width:110px;height:60px"></div>
<div class="abs corner-ornament" role="img" aria-label="Faint green leaf ornament" style="left:855px;top:420px;width:110px;height:60px"></div>
<h2 class="abs col-title" style="left:83px;top:447px">Plan Buckets to Include</h2>
<p class="abs col-text">Lorem Ipsum is simply dummy text of the printing and typesetting industry. Lorem Ipsum has been the industry's standard dummy text ever since the 1500s, when an unknown printer took a galley of type and scrambled it to make a type specimen book. It has survived not only five centuries</p>
<a class="abs read-more">Read more &#9656;</a>
<div class="abs v-rule" style="left:322px;top:470px;height:140px"></div>
<h2 class="abs col-title" style="left:362px;top:447px">The $5 Quest</h2>
<div class="abs video" role="img" aria-label="Explanation video still: group photo of students outdoors"></div>
<div class="abs video-bar"></div>
<div class="abs v-rule" style="left:623px;top:470px;height:140px"></div>
<h2 class="abs col-title" style="left:665px;top:447px">See our pamphlets</h2>
<div class="abs pamphlets" role="img" aria-label="Fan of four colourful program pamphlets"></div>

<!-- blog and queries -->
<div class="abs panel"></div>
<svg class="abs" style="left:95px;top:632px" width="32" height="46" role="img" aria-label="Pencil icon"><rect x="12" y="4" width="10" height="32" rx="2" fill="#8cb82a" transform="rotate(15 17 20)"/><polygon points="10,36 18,38 11,45" fill="#555"/></svg>
<h2 class="abs sec-title" style="left:134px;top:648px">Latest <span>Blog</span></h2>
<h3 class="abs blog-sub" style="font-weight:400">Lorum ipsum is simply a dummy text since 1500</h3>
<p class="abs blog-text">Lorem Ipsum is simply dummy text of the printing and typesetting industry. Lorem Ipsum has been the industry's standard dummy text ever since the 1500s, when an unknown printer took a galley of type and scrambled it to make a type specimen book. It has survived not only five centuries .</p>
<div class="abs blog-meta">Readmore[+] &nbsp;&nbsp;|&nbsp;&nbsp; 1 comment</div>
<div class="abs tweet"><span class="pill"><i></i>Tweet</span><span class="count">1</span></div>
<div class="abs dash-rule"></div>
<div class="abs q-icon">?</div>
<h2 class="abs sec-title" style="left:668px;top:652px">Ask <span>Queries</span></h2>
<span class="abs form-label" style="top:699px">Name</span>
<div class="abs field" style="top:697px"></div>
<span class="abs form-label" style="top:727px">Phone</span>
<div class="abs field" style="top:725px"></div>
<span class="abs form-label" style="top:755px">Query</span>
<div class="abs field" style="top:753px;height:41px"></div>
<div class="abs submit">Submit</div>

<!-- events -->
<svg class="abs" style="left:104px;top:855px" width="28" height="26"><path d="M4 8 L14 2 L14 6 Q24 8 22 24 Q18 12 14 12 L14 16 Z" fill="var(--green)"/></svg>
<h2 class="abs sec-title" style="left:143px;top:857px;font-size:20px">Our Event <span>Photo's</span></h2>
<div class="abs event-photo" style="left:98px;background:linear-gradient(#3c5fa0,#2b3550 60%,#7aa7c8)" role="img" aria-label="Event photo: exhibition hall with display stand"></div>
<div class="abs event-photo" style="left:246px;background:linear-gradient(#6a3a1e,#2a1a12 60%,#5a4530)" role="img" aria-label="Event photo: crowded evening gathering"></div>
<div class="abs event-photo" style="left:396px;background:linear-gradient(#b8ada0,#8a8070 60%,#d8d2c6)" role="img" aria-label="Event photo: conference room presentation"></div>
<div class="abs event-photo" style="left:549px;background:linear-gradient(#8a2030,#c06060 50%,#e8e6e2)" role="img" aria-label="Event photo: speaker addressing seated audience"></div>
<div class="abs event-photo" style="left:707px;background:linear-gradient(#3c5fa0,#2b3550 60%,#7aa7c8)" role="img" aria-label="Event photo: exhibition hall with display stand"></div>

<!-- footer -->
<footer class="abs footer"></footer>
<div class="abs footer-top"></div>
<h2 class="abs f-title" style="left:69px">All Links</h2>
<ul class="abs f-links">
  <li>About</li>
  <li>Why Request $5 Quest</li>
  <li>Success Stories</li>
  <li>Partners</li>
</ul>
<div class="abs v-rule" style="left:236px;top:1040px;height:110px"></div>
<h2 class="abs f-title" style="left:271px">Testimonials</h2>
<span class="abs quote-open">&ldquo;</span>
<p class="abs quote"><b>Lorem Ipsum is simply dummy text of the printing and typesetting industry.</b> Lorem Ipsum has been the industry's</p>
<span class="abs quote-close">&rdquo;</span>
<div class="abs author">Dale Mercer</div>
<div class="abs v-rule" style="left:487px;top:1040px;height:110px"></div>
<h2 class="abs f-title" style="left:525px">Our&nbsp; Sponsers</h2>
<div class="abs badge" style="left:530px;top:1082px;width:38px;height:14px;border-radius:2px"></div>
<div class="abs badge" style="left:575px;top:1072px;width:34px;height:34px;background:#b9d23a"></div>
<div class="abs badge" style="left:617px;top:1075px;width:22px;height:28px;border-radius:3px"></div>
<div class="abs badge" style="left:530px;top:1124px;width:38px;height:16px;border-radius:2px"></div>
<div class="abs badge" style="left:575px;top:1114px;width:34px;height:34px;background:#cfe0ee"></div>
<div class="abs badge" style="left:617px;top:1126px;width:30px;height:12px;border-radius:2px"></div>
<div class="abs v-rule" style="left:693px;top:1040px;height:110px"></div>
<h2 class="abs f-title" style="left:721px">Contact Us</h2>
<div class="abs contact">
  $5 quest student program<br>
  Linmoor 4810 Eastern Province<br>
  &nbsp;Ph &nbsp;&nbsp;&nbsp;&nbsp;: &nbsp;&nbsp;(08) 9000 1234<br>
  &nbsp;Email : &nbsp;info@questprogram.example
</div>
<div class="abs follow">Follow us : -</div>
<div class="abs social" style="left:825px;background:#3b5a98" aria-label="Social A"></div>
<div class="abs social" style="left:856px;background:#3a9fd8" aria-label="Social B"></div>
<div class="abs social" style="left:886px;background:#1f6fa8" aria-label="Social C"></div>
<div class="abs copyright">Copyright @&nbsp; $5 quest program.example, All Right Reserved</div>

</body>
</html>
```